Create Social Media design templates for Online-Education-Startup

We are an online platform for pupils who provide group courses and on demand individual tutroing lessons. Our core values are personalisation, family and success. We need a holistic social media design concept which includes nine possible layouts for Instagram posts which reflect our values and promote not only our offerings and special deals but also support in building our brand image (for example: telling company history, daily news, funny facts, getting to know the team etc.).
Additionally, we need design elements for our YouTube channel:
-Videocover
-Cover Image for the channel

Our main colour is orange (RGB-Code: 255;105;31) and additional colours white, black, and grey. For the reference have a look at our website: www.lernvolta.de.

Target Market(s)

We want to attract customers to our online tutoring courses and build a brand.

Industry/Entity Type

Education / Tutoring

Font styles to use
Sans Serif

Requirements
Must have
• Familiarize yourself with the style of our website. The designs should fit as well as possible.

```html
<!DOCTYPE html>
<html lang="de">
<head>
<meta charset="utf-8">
<title>LernVolta – YouTube Designs</title>
<link href="https://fonts.googleapis.com/css2?family=Anton&family=Poppins:ital,wght@0,400;0,500;0,600;0,700;1,600;1,800&display=swap" rel="stylesheet">
<style>
  :root {
    --orange: #ff691f;
    --orange-deep: #f26a05;
    --orange-light: #ff9a2a;
    --red-orange: #ee3b0c;
    --band-orange: #e8682e;
    --fold-orange: #c24a1c;
    --yellow: #fde047;
    --ink: #111111;
    --white: #ffffff;
    --paper: #f2f2f2;
  }
  * { box-sizing: border-box; margin: 0; padding: 0; }
  html, body { width: 1200px; height: 849px; overflow: hidden; background: var(--white); }
  body { position: relative; font-family: "Poppins", sans-serif; }

  .card {
    position: absolute; left: 284px; width: 589px; height: 332px;
    overflow: hidden; box-shadow: 0 3px 10px rgba(0,0,0,.35);
  }

  /* ---------- Video cover ---------- */
  .cover { top: 73px;
    background:
      radial-gradient(circle at 83% 18%, #fff6e8 0%, #ffc276 14%, rgba(255,140,20,0) 42%),
      linear-gradient(135deg, #ff7a00 0%, var(--orange-deep) 55%, #e85f00 100%);
  }
  .cover .chevrons { position: absolute; left: 186px; top: 16px; }
  .headline {
    position: absolute; left: 44px; top: 48px;
    transform: rotate(-8deg); transform-origin: left top;
    font-family: "Anton", sans-serif; text-transform: uppercase; line-height: 1;
  }
  .headline .pill {
    display: block; width: max-content; color: var(--ink);
    border-radius: 24px; padding: 4px 18px 2px 22px; font-size: 38px;
    box-shadow: 3px 4px 6px rgba(120,40,0,.35);
  }
  .pill--light { background: var(--orange-light); }
  .pill--red { background: var(--red-orange); color: var(--white) !important; margin: -2px 0 0 2px; padding-right: 14px !important; }
  .headline .pill--red { color: var(--white); }
  .pill--light.pill--last { margin-top: -2px; }
  .cover .tagline {
    position: absolute; left: 84px; top: 242px; width: 190px;
    transform: rotate(-12deg); transform-origin: left top;
    font-family: Arial, Helvetica, sans-serif; font-weight: 700; font-size: 11.5px;
    letter-spacing: .4px; line-height: 1.55; color: var(--white); text-align: center;
  }
  .brand { position: absolute; display: flex; align-items: center; }
  .brand .mark { border-radius: 50%; border: 3px solid var(--orange); flex: none; }
  .brand .name { font-weight: 700; color: var(--ink); line-height: 1.1; }
  .brand .sub { font-weight: 400; color: var(--ink); line-height: 1.2; }
  .cover .brand { left: 445px; top: 49px; gap: 4px; }
  .cover .brand .mark { width: 36px; height: 32px; }
  .cover .brand .name { font-size: 11px; }
  .cover .brand .sub { font-size: 10px; }
  .cover .illustration {
    position: absolute; left: 287px; top: 128px; width: 290px; height: 204px;
    border-radius: 50% 50% 0 0 / 40% 40% 0 0;
    background: radial-gradient(ellipse at 50% 75%, #f4f4f4 0%, #f6d36a 30%, rgba(240,120,20,0) 70%);
  }
  .cover .icon-cluster {
    position: absolute; left: 0; top: 250px; width: 86px; height: 82px;
    border-radius: 0 50% 0 0;
    background: radial-gradient(circle at 45% 55%, #7fd6c4 0%, #c56ad6 35%, rgba(255,120,20,0) 72%);
  }

  /* ---------- Channel banner ---------- */
  .banner { top: 471px;
    background: repeating-linear-gradient(135deg, #f7f7f7 0 30px, #ececec 30px 60px);
  }
  .banner .yellow-field { position: absolute; inset: 0; }
  .banner .title-band { position: absolute; inset: 0; }
  .banner .title {
    position: absolute; left: 38px; top: 88px; width: 330px; text-align: center;
    font-weight: 800; font-style: italic; font-size: 55px; letter-spacing: -1px;
    color: var(--yellow); line-height: 1;
  }
  .banner .subtitle {
    position: absolute; left: 60px; top: 149px; width: 290px; text-align: center;
    font-weight: 600; font-style: italic; font-size: 16px; color: var(--white); line-height: 1.5;
  }
  .banner .body-copy {
    position: absolute; left: 42px; top: 222px; width: 270px;
    font-weight: 500; font-size: 14px; line-height: 1.45; color: var(--ink); letter-spacing: -.2px;
  }
  .banner .cta {
    position: absolute; left: 42px; top: 294px; width: 126px; height: 24px;
    background: var(--yellow); clip-path: polygon(6% 0, 100% 0, 94% 100%, 0 100%);
    font-weight: 700; font-size: 13px; color: var(--ink);
    display: flex; align-items: center; justify-content: center;
  }
  .banner .brand { left: 413px; top: 9px; gap: 6px; }
  .banner .brand .mark { width: 46px; height: 40px; }
  .banner .brand .name { font-size: 13px; }
  .banner .brand .sub { font-size: 12px; }
  .banner .photo {
    position: absolute; left: 286px; top: 84px; width: 303px; height: 248px;
    clip-path: polygon(14% 38%, 30% 4%, 100% 0, 100% 100%, 0 100%, 0 70%);
    background: linear-gradient(100deg, #3a3032 0%, #b97fd0 25%, #e8c9a8 45%, #3e3036 60%, #e3a28a 75%, #f178ad 100%);
  }
</style>
</head>
<body>

  <section class="card cover" aria-label="Video-Cover">
    <svg class="chevrons" width="44" height="36" viewBox="0 0 44 36" aria-hidden="true">
      <path d="M4 8 L16 10 L10 20" fill="none" stroke="var(--red-orange)" stroke-width="4"/>
      <path d="M16 4 L28 6 L22 16" fill="none" stroke="var(--red-orange)" stroke-width="4"/>
      <path d="M28 0 L40 2 L34 12" fill="none" stroke="var(--red-orange)" stroke-width="4"/>
    </svg>

    <h1 class="headline">
      <span class="pill pill--light">Entfessle</span>
      <span class="pill pill--red">Dein Lernpotenzial</span>
      <span class="pill pill--light pill--last">Mit LernVolta</span>
    </h1>

    <p class="tagline">Personalisierte Nachhilfe, um dir zum schulischen Erfolg zu verhelfen.</p>

    <div class="brand">
      <span class="mark" aria-hidden="true"></span>
      <div>
        <div class="name">LernVolta</div>
        <div class="sub">Bildungsinstitut</div>
      </div>
    </div>

    <div class="illustration" role="img" aria-label="Illustration: offenes Buch mit Glühbirne, Doktorhut, Globus, Taschenrechner, Stiften und Wissenschaftssymbolen"></div>
    <div class="icon-cluster" role="img" aria-label="Illustration: Atommodell mit bunten Lern-Icons"></div>
  </section>

  <section class="card banner" aria-label="Kanal-Titelbild">
    <svg class="yellow-field" width="589" height="332" viewBox="0 0 589 332" aria-hidden="true">
      <polygon points="395,0 589,0 589,332 300,332" fill="var(--yellow)"/>
    </svg>
    <svg class="title-band" width="589" height="332" viewBox="0 0 589 332" aria-hidden="true">
      <polygon points="358,17 391,17 406,58 342,58" fill="var(--fold-orange)"/>
      <polygon points="0,202 18,202 0,248" fill="var(--fold-orange)"/>
      <polygon points="0,58 412,58 385,202 0,202" fill="var(--band-orange)"/>
    </svg>

    <div class="title">LERNVOLTA</div>
    <div class="subtitle">DEIN WEG ZUM SCHULISCHEN ERFOLG</div>

    <p class="body-copy">Experten-Nachhilfe, personalisiertes Lernen und ein familienorientierter Ansatz.</p>
    <div class="cta">WATCH NOW</div>

    <div class="photo" role="img" aria-label="Foto: drei lächelnde Schülerinnen mit Rucksack, Heften und Tablet"></div>

    <div class="brand">
      <span class="mark" aria-hidden="true"></span>
      <div>
        <div class="name">LernVolta</div>
        <div class="sub">Bildungsinstitut</div>
      </div>
    </div>
  </section>

</body>
</html>
```